Business cards and stationary design

We just completed the design of our new logo and we need to print new business cards and letterhead for our nonprofit. We are looking for a fresh new design that shows off our new logo. On letterhead, we must have a column on the right or left to include our Board of Directors (up to 45 names) (see attachment)

Industry/Entity Type

Non-Profit

Contact Information for Business Card

Standard business card with name, title, Company name, mailing address phone numbers, email address and website. Tagline on back "Bringing the homeless home"

Font styles to use
Sans Serif

Requirements
Must have
• include pertinent information above
• new logo
• fonts compatible with logo
• should use logo colors only
Nice to have
• tag lines

```html
<!DOCTYPE html>
<html lang="en">
<head>
<meta charset="utf-8">
<title>Shelter Bridge Alliance – Business Card</title>
<link href="https://fonts.googleapis.com/css2?family=Work+Sans:wght@400;500;600&display=swap" rel="stylesheet">
<style>
  :root {
    --backdrop: #2b2b2d;
    --card: #1c1c1e;
    --brand-teal: #1a8fb0;
    --brand-red: #e3202b;
    --brand-yellow: #f5b320;
    --ink: #f2f2f2;
  }
  * { box-sizing: border-box; margin: 0; padding: 0; }
  html, body {
    width: 1200px; height: 900px; overflow: hidden;
    background: var(--backdrop);
    font-family: "Work Sans", sans-serif;
  }
  .canvas {
    width: 1200px; height: 900px;
    display: flex; flex-direction: column; align-items: center; justify-content: center;
    gap: 40px;
  }
  .card {
    width: 700px; height: 400px;
    background: var(--card);
    position: relative;
    box-shadow: 0 12px 30px rgba(0,0,0,0.45);
  }
  .card--front {
    display: flex; align-items: center; justify-content: center;
  }
  .brand-name {
    color: var(--brand-teal);
    font-weight: 600;
    font-size: 40px;
    letter-spacing: 3px;
    text-transform: uppercase;
    display: flex; align-items: center; gap: 16px;
  }
  .brand-name .brand-dot {
    width: 22px; height: 22px; border-radius: 50%;
    background: var(--brand-teal);
    flex: none;
  }
  .card--back .brand-name {
    position: absolute; left: 52px; top: 170px;
    font-size: 26px; letter-spacing: 2px;
    width: 290px; flex-wrap: nowrap;
  }
  .card--back .brand-name span { line-height: 1.25; }
  .divider {
    position: absolute; left: 372px; top: 118px;
    width: 3px; height: 164px;
    background: var(--brand-yellow);
  }
  .contact {
    position: absolute; left: 402px; top: 118px;
    color: var(--ink);
  }
  .contact__name {
    color: var(--brand-yellow);
    font-weight: 500; font-size: 26px; text-transform: uppercase;
    letter-spacing: 0.5px;
  }
  .contact__title { font-size: 18px; margin-top: 2px; }
  .contact__address { font-size: 18px; margin-top: 12px; line-height: 1.3; }
  .contact__list { list-style: none; margin-top: 8px; font-size: 18px; line-height: 1.4; }
  .contact__list li { display: flex; align-items: center; gap: 8px; }
  .contact__list svg { width: 14px; height: 14px; flex: none; }
</style>
</head>
<body>
<main class="canvas">
  <section class="card card--front" aria-label="Card front">
    <div class="brand-name"><span class="brand-dot"></span>Shelter Bridge Alliance</div>
  </section>

  <section class="card card--back" aria-label="Card back">
    <div class="brand-name"><span class="brand-dot"></span><span>Shelter Bridge<br>Alliance</span></div>
    <div class="divider"></div>
    <div class="contact">
      <p class="contact__name">Daniel Reyes</p>
      <p class="contact__title">Director</p>
      <p class="contact__address">P.O. Box 52690,<br>Austin, Texas 78701</p>
      <ul class="contact__list">
        <li>
          <svg viewBox="0 0 16 16" aria-hidden="true"><path d="M4 1l3 3-2 2c1 2 3 4 5 5l2-2 3 3-2 3C7 14 2 9 1 3z" fill="var(--brand-yellow)"/></svg>
          512.555.0187
        </li>
        <li>
          <svg viewBox="0 0 16 16" aria-hidden="true"><rect x="1.5" y="3.5" width="13" height="9" fill="none" stroke="var(--brand-yellow)" stroke-width="1.4"/><path d="M1.5 3.5l6.5 5 6.5-5" fill="none" stroke="var(--brand-yellow)" stroke-width="1.4"/></svg>
          info@sbaaustin.org
        </li>
        <li>
          <svg viewBox="0 0 16 16" aria-hidden="true"><circle cx="8" cy="8" r="6.5" fill="none" stroke="var(--brand-yellow)" stroke-width="1.4"/><path d="M1.5 8h13M8 1.5c-3 3.5-3 9.5 0 13M8 1.5c3 3.5 3 9.5 0 13" fill="none" stroke="var(--brand-yellow)" stroke-width="1.2"/></svg>
          www.sbaaustin.org
        </li>
      </ul>
    </div>
  </section>
</main>
</body>
</html>
```